Brenwick Structures Construction Company Seeking Modern Website

We are a small construction company wanting to create a web presence. We don't have much in the way of current content but will get photos as they come in. Attached is a picture of our business card.
The pages we would like on the menu are:
Home
Portfolio
Product Specs
Testimonials
Our Process
Contact
Some designs we like are:
http://www.tovasheds-example.com/
http://www.qrnstructures-example.com/
http://dunholtbarns-example.com/
http://pellingframes-example.com/
Not much requirements other than that so feel free to be creative!
Updates
Target Market(s)
Construction
Commercial and Residential Buildings
Industry/Entity Type
Construction Company
Number of Pages Required
5+ page
Look and feel

```html
<!DOCTYPE html>
<html lang="en">
<head>
<meta charset="utf-8">
<title>Brenwick Structures</title>
<link href="https://fonts.googleapis.com/css2?family=Roboto:ital,wght@0,300;0,400;0,500;1,300;1,400&family=Roboto+Condensed:wght@400;500&display=swap" rel="stylesheet">
<style>
:root{
  --red:#d2312a;
  --ink:#333;
  --muted:#6f6f6f;
  --line:#d8d8d8;
  --band:#eeeeee;
  --foot:#f1f1f1;
  --blue:#1e9ad6;
}
*{box-sizing:border-box;margin:0;padding:0}
html,body{width:807px;height:1200px;overflow:hidden;background:#fff}
body{position:relative;font-family:"Roboto",sans-serif;color:var(--ink)}
.abs{position:absolute}
/* header */
.brand{left:40px;top:32px;font:500 24px/1 "Roboto Condensed",sans-serif;color:var(--red);display:flex;align-items:center;gap:8px}
.brand-dot{width:14px;height:14px;border-radius:50%;background:var(--red)}
.toplinks{right:40px;top:25px;display:flex;align-items:center;font-size:10.5px;color:#888}
.toplinks span{padding:0 8px;border-left:1px solid #ddd}
.toplinks span:first-child{border:0}
.toplinks .hot{color:var(--red)}
.toplinks .phone{color:#222;font-size:12.5px;padding-left:4px;border:0}
.toplinks svg{margin-left:6px}
.nav{right:40px;top:53px;display:flex;gap:29px;font-size:11px;color:#333}
.nav .on{color:var(--red)}
/* hero */
.hero{left:0;top:88px;width:807px;height:324px}
.caption{left:14px;top:308px;width:332px;height:64px;border-radius:50%;background:rgba(214,60,48,.85);color:#fff;font:500 14px/20px "Roboto Condensed",sans-serif;text-align:center;padding-top:12px;padding-left:30px}
.dots{display:flex;gap:4px}
.dots i{width:8px;height:8px;border-radius:50%;border:1px solid #fff;display:block}
.dots i.on{background:#fff}
/* services */
.services{left:0;top:412px;width:807px;height:102px}
.svc-title{font-size:14.5px;color:var(--red)}
.svc-text{font-size:8.6px;line-height:16px;color:var(--muted)}
.ring{width:56px;height:56px;border-radius:50%;border:1.5px solid var(--red);display:flex;align-items:center;justify-content:center;background:#fafafa}
/* welcome */
.h2{font-size:19px;color:var(--red);text-align:center;width:807px;left:0}
.welcome-text{left:80px;width:647px;top:583px;font-size:8.8px;line-height:18.5px;color:var(--muted);text-align:center}
/* process */
.process{left:0;top:664px;width:807px;height:235px;background:var(--band)}
.step{width:152px;text-align:center;top:724px}
.step .pic{width:116px;height:116px;border-radius:50%;margin:0 auto;border:1.5px solid #222}
.step.on .pic{border:2px solid var(--red)}
.step p{margin-top:11px;font-size:12.5px;color:#333}
.step.on p{color:var(--red)}
/* testimonial */
.avatar{left:85px;top:957px;width:56px;height:56px;border-radius:50%;border:1px solid #bbb;background:linear-gradient(180deg,#d9b487,#b98b57)}
.quote-text{left:228px;top:966px;font-style:italic;font-weight:300;font-size:9px;line-height:19px;color:#555}
.quote-name{left:228px;top:1005px;font-style:italic;font-size:10.5px;color:var(--red)}
.tdots{left:677px;top:1008px;display:flex;gap:4px}
.tdots i{width:8px;height:8px;border-radius:50%;border:1px solid #333;display:block}
.tdots i.on{background:var(--blue);border-color:var(--blue)}
/* footer */
.footer{left:0;top:1058px;width:807px;height:142px;background:var(--foot);border-top:2px solid #e0e0e0}
.f-head{top:1075px;font-size:14px;color:var(--red)}
.f-rule{top:1078px;width:1px;height:104px;background:var(--line)}
.social{left:53px;top:1106px;display:grid;grid-template-columns:16px 16px;gap:6px 7px}
.social i{width:16px;height:16px;border-radius:50%;display:block}
.contact{left:120px;top:1106px;font-size:9px;color:#222;width:150px}
.contact .row{display:flex;align-items:center;gap:8px;margin-top:8px;font-size:10.5px;color:#555;white-space:nowrap}
.contact .row.ph{color:#222;font-size:12px}
.small{font-size:8.3px;line-height:14.5px;color:var(--muted)}
.zip{left:303px;top:1136px;width:131px;height:22px;border:1px solid #ddd;background:#fff;font-size:6.5px;color:#aaa;padding:7px 6px}
.locate{left:440px;top:1136px;width:65px;height:22px;background:var(--blue);color:#fff;font-size:9px;font-weight:500;text-align:center;line-height:22px}
.news-title{left:542px;top:1105px;font-size:8.8px;color:#222}
.more{left:542px;top:1155px;font-size:8.5px;font-style:italic;color:var(--blue)}
</style>
</head>
<body>

<header>
  <div class="abs brand"><span class="brand-dot"></span>Brenwick Structures</div>
  <div class="abs toplinks">
    <span>Location</span><span>FAQ's</span><span class="hot">Contact us</span><span>Call us Today</span><span class="phone">0123 555 018</span>
    <svg width="9" height="14" viewBox="0 0 9 14"><rect x="1" y="1" width="7" height="12" rx="1.5" fill="none" stroke="#d2312a" stroke-width="1.5"/><rect x="3.5" y="10" width="2" height="1.2" fill="#d2312a"/></svg>
  </div>
  <nav class="abs nav"><span class="on">Home</span><span>Portfolio</span><span>Product Specs</span><span>Testimonials</span><span>Our Process</span><span>Contact</span></nav>
</header>

<svg class="abs hero" viewBox="0 0 807 324" role="img" aria-label="Photo of a wooden building on open prairie under a blue sky">
  <defs>
    <linearGradient id="sky" x1="0" y1="0" x2="0" y2="1">
      <stop offset="0" stop-color="#5580bd"/><stop offset=".6" stop-color="#a9c0d8"/><stop offset="1" stop-color="#b39866"/>
    </linearGradient>
  </defs>
  <rect width="807" height="324" fill="url(#sky)"/>
  <path d="M0 0H807V10Q404 -6 0 12Z" fill="#fff"/>
  <path d="M0 12Q404 -6 807 10" fill="none" stroke="#333" stroke-width="1.2"/>
  <line x1="0" y1="323.5" x2="807" y2="323.5" stroke="#333"/>
</svg>
<div class="abs caption">We Provide Commercial Construction<br>and Residential Buildings.</div>
<div class="abs dots" style="left:388px;top:391px"><i></i><i class="on"></i><i></i></div>

<svg class="abs services" viewBox="0 0 807 102" aria-hidden="true">
  <defs><linearGradient id="sv" x1="0" y1="0" x2="0" y2="1"><stop offset="0" stop-color="#f6f6f6"/><stop offset="1" stop-color="#ececec"/></linearGradient></defs>
  <path d="M0 0H807V92Q404 110 0 92Z" fill="url(#sv)"/>
  <path d="M0 92Q404 110 807 92" fill="none" stroke="#d0d0d0"/>
  <line x1="404" y1="4" x2="404" y2="98" stroke="#dcdcdc"/>
</svg>
<div class="abs svc-title" style="right:502px;top:432px">Commercial Construction</div>
<div class="abs svc-text" style="right:502px;top:457px;text-align:right">Lorem ipsum dolor sit amet, consectetur adipiscing elit do<br>.eiusmod tempor incididunt ut labore aliqua</div>
<div class="abs ring" style="left:325px;top:436px">
  <svg width="20" height="26" viewBox="0 0 20 26"><rect x="1" y="1" width="18" height="24" fill="none" stroke="#d2312a" stroke-width="2"/><g fill="#d2312a"><rect x="5" y="5" width="3" height="3"/><rect x="12" y="5" width="3" height="3"/><rect x="5" y="11" width="3" height="3"/><rect x="12" y="11" width="3" height="3"/><rect x="8" y="18" width="4" height="7"/></g></svg>
</div>
<div class="abs ring" style="left:425px;top:436px">
  <svg width="26" height="22" viewBox="0 0 26 22"><path d="M13 1L1 11h3v10h7v-6h4v6h7V11h3z" fill="#d2312a"/></svg>
</div>
<div class="abs svc-title" style="left:502px;top:432px">Residential Buildings</div>
<div class="abs svc-text" style="left:503px;top:457px">Lorem ipsum dolor sit amet, consectetur adipiscing elit do<br>eiusmod tempor incididunt ut labore aliqua.</div>

<h2 class="abs h2" style="top:548px;font-weight:400">Welcome to Brenwick Structures</h2>
<p class="abs welcome-text">Lorem ipsum dolor sit amet, consectetur adipiscing elit, sed do eiusmod tempor incididunt ut labore et dolore magna aliqua. . Duis aute irure dolor in reprehenderit in voluptate velit esse cillum dolore eu fugiat nulla pariatur. Excepteur sint occaecat cupidatat non proident sunt ut enim ad minim veniam, quis nostrud exercitation ullamco laboris nisi ut aliquip ex ea &nbsp;aute irure dolor in reprehenderit in voluptate velit esse &nbsp;commodo consequat.</p>

<section class="abs process"></section>
<h2 class="abs h2" style="top:683px;font-weight:400">Our Process</h2>
<div class="abs step on" style="left:102px"><div class="pic" role="img" aria-label="Photo of a timber house frame under construction" style="background:linear-gradient(180deg,#c99a5e,#b8773a)"></div><p>Eiusmod tempor</p></div>
<div class="abs step" style="left:255px"><div class="pic" role="img" aria-label="Photo of new homes being built" style="background:linear-gradient(180deg,#c4c0bb,#a08670)"></div><p>Eiusmod tempor</p></div>
<div class="abs step" style="left:407px"><div class="pic" role="img" aria-label="Photo of a farm barn with silos" style="background:linear-gradient(180deg,#7d9cc8,#b0603e)"></div><p>Eiusmod tempor</p></div>
<div class="abs step" style="left:559px"><div class="pic" role="img" aria-label="Photo of a brick house nearing completion" style="background:linear-gradient(180deg,#8f7a68,#6f8f4c)"></div><p>Eiusmod tempor</p></div>

<div class="abs avatar" role="img" aria-label="Portrait of the client giving the testimonial"></div>
<svg class="abs" style="left:155px;top:948px" width="70" height="74" viewBox="0 0 70 74" aria-hidden="true">
  <path d="M14 2Q4 2 4 12V28Q4 36 0 37Q4 38 4 46V62Q4 72 14 72" fill="none" stroke="#555" stroke-width="2.5"/>
  <g fill="#bbb"><circle cx="34" cy="22" r="7"/><path d="M27 22Q27 8 40 5L41 8Q32 11 32 20Z"/><circle cx="55" cy="22" r="7"/><path d="M48 22Q48 8 61 5L62 8Q53 11 53 20Z"/></g>
</svg>
<p class="abs quote-text">Lorem ipsum dolor sit amet, consectetur adipiscing elit, sed do eiusmod tempor incididunt ut labore et dolore magna aliqua.<br>Duis aute irure dolor in reprehenderit in voluptate velit esse cillum dolore eu fugiat nulla pariatur.</p>
<p class="abs quote-name">Marla Quint</p>
<div class="abs tdots"><i></i><i class="on"></i><i></i></div>

<footer class="abs footer"></footer>
<h3 class="abs f-head" style="left:53px;font-weight:400">Keep in Touch</h3>
<div class="abs f-rule" style="left:281px"></div>
<h3 class="abs f-head" style="left:300px;font-weight:400">Office Locator</h3>
<div class="abs f-rule" style="left:523px"></div>
<h3 class="abs f-head" style="left:541px;font-weight:400">Latest News</h3>
<svg class="abs" style="left:746px;top:1077px" width="22" height="12" viewBox="0 0 22 12" aria-hidden="true"><path d="M6 1L1 6l5 5M16 1l5 5-5 5" fill="none" stroke="#222" stroke-width="1.6"/></svg>

<div class="abs social">
  <i style="background:#2b4f8f"></i><i style="background:#2a9ad6"></i>
  <i style="background:#d44a37"></i><i style="background:#c8232c"></i>
  <i style="background:#1f3f7a"></i><i style="background:#f29b2b"></i>
</div>
<div class="abs contact">
  <div>CONTACT US</div>
  <div class="row"><svg width="10" height="8" viewBox="0 0 10 8"><rect width="10" height="8" fill="#222"/><path d="M0 0l5 4 5-4" fill="none" stroke="#fff" stroke-width="1"/></svg>info@brenwick-example.com</div>
  <div class="row ph"><svg width="7" height="11" viewBox="0 0 7 11"><rect x=".75" y=".75" width="5.5" height="9.5" rx="1" fill="none" stroke="#222" stroke-width="1.5"/></svg>0123 555 018</div>
</div>

<p class="abs small" style="left:302px;top:1100px">Lorem ipsum dolor sit amet, consectetur adipiscing elit,<br>sed do eiusmod tempor .....</p>
<div class="abs zip">Enter Zip Code</div>
<div class="abs locate">LOCATE</div>

<div class="abs news-title">LOREM IPSUM DOLOR SIT AMET NSECTETUR</div>
<p class="abs small" style="left:542px;top:1121px">Lorem ipsum dolor sit amet, consectetur adipiscing elit,<br>eiusmod tempor incididunt.....</p>
<div class="abs more">Read More</div>

</body>
</html>
```